Bright Horizon Games Fundraising Event- Climb Along Today!

Create a postcard that can be printed, and also repurposed for website graphics- this is an invitation and the call to action is to visit our website and purchase tickets.
Project brief is attached.
Bright Horizon National Games logo is attached.
Leave space for a sponsor logo to be added.
This is a once in a lifetime opportunity to ride the Harborview Sky Loop with some of the biggest names in Seattle!
Design should convey a sense of urgency to get ride tickets with celebrity of their choice.
Images for use are included.
Target Market(s)
Bright Horizon Games Supporters, Fans of our Celebrity Guests, Fans of outdoor/live music
Industry/Entity Type
Non Profit
Font styles to use
Other font styles liked:
- Ubuntu or Arial
Requirements
Must have
- Event name, date, time, location, National Games logo
- Space to add a sponsor logo at a later time
Nice to have
- Creative way to show the 2 different purchase prices and benefits

```html
<!DOCTYPE html>
<html lang="en">
<head>
<meta charset="utf-8">
<title>Bright Horizon Games – Climb Along Today! Postcard</title>
<link href="https://fonts.googleapis.com/css2?family=Ubuntu:wght@400;500;700&family=Arimo:wght@400;700&display=swap" rel="stylesheet">
<style>
  :root {
    --teal: #33b497;
    --teal-light: #3cc0a2;
    --purple: #4a52a6;
    --plum: #5b2a86;
    --paper: #eef0f1;
    --white: #ffffff;
    --ink: #1f2a2a;
    --stage: #e8e5e0;
  }
  * { box-sizing: border-box; margin: 0; padding: 0; }
  html, body { width: 1200px; height: 900px; overflow: hidden; }
  body { background: var(--stage); font-family: "Ubuntu", Arial, sans-serif; position: relative; }

  .postcard { position: absolute; top: 257px; width: 505px; height: 388px; overflow: hidden; box-shadow: 2px 3px 6px rgba(0,0,0,.35); }
  .postcard--front { left: 65px; background: var(--paper); }
  .postcard--back { left: 632px; background: var(--white); }
  .postcard svg.shapes { position: absolute; inset: 0; }

  /* Front */
  .brand { position: absolute; display: flex; align-items: center; gap: 7px; color: var(--plum); font-weight: 500; font-size: 11px; line-height: 1.15; }
  .brand__dot { width: 20px; height: 20px; border-radius: 50%; background: var(--teal); flex: none; }
  .postcard--front .brand { left: 340px; top: 16px; }

  .invite { position: absolute; left: 319px; top: 86px; width: 180px; color: var(--white); }
  .invite__title { font-weight: 700; font-size: 14.5px; line-height: 18px; margin-bottom: 2px; }
  .invite__line { font-size: 12px; line-height: 16.6px; white-space: nowrap; }

  .sponsor { position: absolute; left: 267px; top: 217px; color: var(--purple); font-weight: 700; font-size: 15px; }

  .cta { position: absolute; right: 22px; top: 312px; text-align: right; color: var(--white); }
  .cta__label { font-weight: 700; font-size: 25px; line-height: 28px; }
  .cta__phone { font-size: 25px; line-height: 32px; }

  .web { position: absolute; left: 25px; top: 352px; display: flex; align-items: center; gap: 5px; color: var(--white); font-size: 12px; }

  /* Back */
  .details { position: absolute; left: 8px; top: 22px; width: 205px; font-family: "Arimo", Arial, sans-serif; }
  .details__title { color: var(--white); font-family: "Ubuntu", Arial, sans-serif; font-weight: 700; font-size: 14.5px; }
  .details__band { color: var(--ink); font-family: "Ubuntu", Arial, sans-serif; font-size: 11px; line-height: 13px; }
  .details__heading { margin-top: 18px; color: var(--purple); font-family: "Ubuntu", Arial, sans-serif; font-weight: 700; font-size: 15px; }
  .ticket { margin-top: 8px; }
  .ticket__name { padding-left: 12px; color: var(--white); font-weight: 700; font-size: 11px; margin-bottom: 3px; }
  .ticket__perks { list-style: none; color: var(--white); font-size: 11px; line-height: 12.8px; }
  .ticket__perks li { position: relative; padding-left: 12px; }
  .ticket__perks li::before { content: ""; position: absolute; left: 1px; top: 3px; width: 3px; height: 6px; border: solid var(--white); border-width: 0 1.5px 1.5px 0; transform: rotate(45deg); }
  .ticket__perks li.cont::before { display: none; }

  .postcard--back .brand { left: 274px; top: 68px; flex-direction: column; text-align: center; width: 80px; gap: 5px; }
  .stamp { position: absolute; left: 382px; top: 32px; width: 80px; height: 86px; border: 1px solid #222; }
  .address-line { position: absolute; left: 226px; width: 250px; height: 1px; background: #555; }
</style>
</head>
<body>

<section class="postcard postcard--front" aria-label="Postcard front">
  <svg class="shapes" width="505" height="388" viewBox="0 0 505 388" aria-hidden="true">
    <defs>
      <linearGradient id="photoTone" x1="0" y1="0" x2="0" y2="1">
        <stop offset="0" stop-color="#4d5f4e"/>
        <stop offset=".35" stop-color="#52b545"/>
        <stop offset=".75" stop-color="#62c24f"/>
        <stop offset="1" stop-color="#d9cdbb"/>
      </linearGradient>
    </defs>
    <rect x="255" y="73" width="250" height="3" fill="var(--teal)"/>
    <rect x="265" y="80" width="240" height="115" fill="var(--purple)"/>
    <rect x="255" y="198" width="250" height="3" fill="var(--teal)"/>
    <path d="M0 0 H188 C 265 45 282 250 160 336 L0 336 Z" fill="var(--teal)"/>
    <path d="M0 0 H180 C 255 48 270 248 150 330 L0 330 Z" fill="url(#photoTone)" role="img" aria-label="Photo of a gymnast mid floor routine in an arena"/>
    <path d="M0 330 C 120 335 240 300 330 270 C 400 248 460 250 505 272 L505 388 L0 388 Z" fill="var(--white)"/>
    <path d="M60 333 C 170 330 260 296 340 268 C 405 246 460 248 505 268" fill="none" stroke="var(--purple)" stroke-width="5"/>
    <path d="M0 316 C 0 316 80 340 170 338 C 260 335 330 300 400 285 C 450 274 485 283 505 290 L505 388 L0 388 Z" fill="var(--teal)"/>
  </svg>

  <div class="brand"><span class="brand__dot"></span><span>Bright Horizon<br>National Games</span></div>

  <div class="invite">
    <p class="invite__title">Climb Along Today!</p>
    <p class="invite__line">A party to benefit for the 2018</p>
    <p class="invite__line">Bright Horizon National Games</p>
    <p class="invite__line">Thursday, May 25</p>
    <p class="invite__line">Seattle Waterfront- Pier 12</p>
    <p class="invite__line">Time- 7:00 pm – 10 pm</p>
  </div>

  <p class="sponsor">Sponsor:</p>

  <div class="cta">
    <p class="cta__label">CALL US</p>
    <p class="cta__phone">1800-555-0142</p>
  </div>

  <p class="web">
    <svg width="14" height="14" viewBox="0 0 14 14" aria-hidden="true">
      <g fill="none" stroke="#fff" stroke-width="1.1">
        <circle cx="7" cy="7" r="6"/><ellipse cx="7" cy="7" rx="2.6" ry="6"/>
        <line x1="1" y1="7" x2="13" y2="7"/><line x1="2" y1="4" x2="12" y2="4"/><line x1="2" y1="10" x2="12" y2="10"/>
      </g>
    </svg>
    www.BrightHorizonGames.org/Party
  </p>
</section>

<section class="postcard postcard--back" aria-label="Postcard back">
  <svg class="shapes" width="505" height="388" viewBox="0 0 505 388" aria-hidden="true">
    <path d="M0 0 H214 C 240 80 188 200 206 285 C 214 330 205 365 212 388 H0 Z" fill="var(--teal)"/>
    <path d="M214 0 C 240 80 188 200 206 285 C 214 330 205 365 212 388" fill="none" stroke="var(--purple)" stroke-width="3"/>
  </svg>

  <div class="details">
    <p class="details__title">Event Details</p>
    <p class="details__band">Live Entertainment provided by:<br>The Harbor Lane Big Band</p>
    <p class="details__heading">Two ways to be there</p>

    <div class="ticket">
      <p class="ticket__name">1.$150 Party Ticket</p>
      <ul class="ticket__perks">
        <li>Entry to party</li>
        <li>Free beer, wine and Hors d'oeuvres</li>
        <li>Mingle with special Celebrity Guests</li>
        <li>Support the Mission of the Bright</li>
        <li class="cont">Horizon National Games</li>
      </ul>
    </div>

    <div class="ticket">
      <p class="ticket__name">2.$250 Ride Ticket</p>
      <ul class="ticket__perks">
        <li>Entry to party</li>
        <li>Free beer, wine and Hors d'oeuvres</li>
        <li>Mingle with special Celebrity Guests</li>
        <li>Support the Mission of the Bright</li>
        <li>Horizon National Games</li>
        <li>Ride the Harborview Sky Loop with</li>
        <li class="cont">a Celebrity Guest of your choice!</li>
      </ul>
    </div>
  </div>

  <div class="brand"><span class="brand__dot"></span><span>Bright Horizon National Games</span></div>

  <div class="stamp"></div>
  <div class="address-line" style="top:197px"></div>
  <div class="address-line" style="top:232px"></div>
  <div class="address-line" style="top:267px"></div>
</section>

</body>
</html>
```